Coral Trek Whitsundays camping

A 4 page Brochure for a tourism product . The product is a day charter through the Whitsundays and overnight camping. www.coraltrekvoyages.com.au
On the first page there needs to be an image of a tent and also some beach. The coral Trek logo on the front page and also the words Island Camping. see filer attached brochure text v1
Updates

Target Market(s)

People camping in the Whitsunday Islands

Industry/Entity Type

camming

Colors
59FF00
82FF00
B8FF75
E3FFCB
F4FFEA
EE7325
F08F49
F5BC92
FAE3D3
FDF4ED
E54698
E96AAD
F1A4CE
F9D9EA
FCEFF6

Requirements
Must have
• Images of camping, front page to have tent image ( image uploaded as front page in file name)
Nice to have
• Like to see the words Island camping on the front page. I will update the text at a later date

```html
<!DOCTYPE html>
<html lang="en">
<head>
<meta charset="utf-8">
<title>Coral Trek Whitsundays Camping Brochure</title>
<link rel="stylesheet" href="https://fonts.googleapis.com/css2?family=Montserrat:wght@400;500;600;700;800&display=swap">
<style>
:root{
  --canvas:#ececec;
  --navy:#0b47a8;
  --deep:#2b4677;
  --bright:#0ba3e8;
  --sky:#5cc6f0;
  --ink:#1d1d1d;
  --muted:#444;
  --card:#ffffff;
  --panel:#e9ecf1;
  --label:#1aa0e0;
}
*{box-sizing:border-box;margin:0;padding:0}
html,body{width:1200px;height:3000px;overflow:hidden;background:var(--canvas);font-family:"Montserrat",sans-serif;color:var(--ink)}
.spread{position:absolute;left:40px;width:1120px;height:724px;overflow:hidden;background:#fff;box-shadow:0 10px 30px rgba(0,0,0,.18)}
.spread--front{top:740px}
.spread--inside{top:1504px}
.spread svg.bg{position:absolute;inset:0}
.brand{position:absolute;display:flex;align-items:center;gap:8px;font-weight:600;color:var(--navy);font-family:"Montserrat",sans-serif}
.brand .dot{width:14px;height:14px;border-radius:50%;background:var(--bright)}
/* package card */
.packages{position:absolute;left:19px;top:30px;width:512px;height:648px;background:var(--card);border-radius:12px;box-shadow:0 2px 10px rgba(0,0,0,.25)}
.package{position:absolute;left:0;width:100%}
.package .shot{position:absolute;left:18px;width:148px;height:122px;border-radius:12px}
.package .price{position:absolute;left:22px;font-size:15px;font-weight:600;line-height:1.05;color:var(--ink)}
.package .info{position:absolute;left:215px;width:270px}
.package h3{font-size:10px;font-weight:700;margin-bottom:8px}
.package ul{list-style:none}
.package li{position:relative;padding-left:14px;font-size:7.2px;line-height:1.3;margin-bottom:6px;color:var(--muted)}
.package li::before{content:"";position:absolute;left:0;top:2px;width:6px;height:6px;border-radius:50%;background:var(--label)}
.extras{position:absolute;left:28px;top:640px;width:170px;height:18px;background:var(--navy);color:#fff;font-size:7px;line-height:18px;padding-left:14px}
.extras-price{position:absolute;left:183px;top:648px;width:46px;height:46px;border-radius:50%;background:#111;color:#fff;font-size:15px;font-weight:600;display:flex;align-items:center;justify-content:center;border:2px solid #fff}
.headline{position:absolute;left:592px;top:462px;color:#fff;text-transform:uppercase}
.headline .lead{font-size:20px;font-weight:500;letter-spacing:.5px}
.headline .big{font-size:38px;font-weight:800;line-height:1.08}
.headline .mid{font-size:30px;font-weight:500;line-height:1.2}
.headline .huge{font-size:44px;font-weight:800;line-height:1.05}
/* inside */
.itinerary{position:absolute;left:45px;top:325px;width:466px;height:200px;background:var(--panel);border-radius:6px}
.itinerary h2{position:absolute;left:216px;top:12px;font-size:20px;font-weight:600;color:var(--label);letter-spacing:1px}
.itinerary .steps{position:absolute;left:216px;top:44px;width:235px}
.itinerary .time{font-size:10px;font-weight:600;color:var(--label);margin:4px 0 2px}
.itinerary p{font-size:7.2px;line-height:1.3;margin-bottom:4px;color:var(--muted)}
.locations{position:absolute;left:595px;top:300px}
.locations h2{font-size:21px;font-weight:700;color:var(--navy);line-height:1;text-transform:uppercase}
.locations table{margin-top:18px;border-collapse:collapse}
.locations td{font-size:10px;padding:4px 0;color:var(--muted)}
.locations td:first-child{width:136px}
.locations tr.gap td{padding-top:12px}
</style>
</head>
<body>

<section class="spread spread--front" aria-label="Outer spread: packages and cover">
  <svg class="bg" viewBox="0 0 1120 724" width="1120" height="724">
    <defs>
      <linearGradient id="coverSky" x1="0" y1="0" x2="0" y2="1"><stop offset="0" stop-color="#f7f7f7"/><stop offset="1" stop-color="#dfe3e6"/></linearGradient>
      <linearGradient id="tentPhoto" x1="0" y1="0" x2="1" y2="1"><stop offset="0" stop-color="#ffd13a"/><stop offset=".5" stop-color="#e9a23a"/><stop offset="1" stop-color="#6a6a66"/></linearGradient>
      <linearGradient id="sunsetPhoto" x1="0" y1="0" x2="0" y2="1"><stop offset="0" stop-color="#1f3f73"/><stop offset=".45" stop-color="#f2a431"/><stop offset="1" stop-color="#b8925a"/></linearGradient>
      <linearGradient id="navyBand" x1="0" y1="0" x2="1" y2="0"><stop offset="0" stop-color="#0a3f9c"/><stop offset="1" stop-color="#1463c8"/></linearGradient>
    </defs>
    <rect x="531" y="0" width="589" height="724" fill="url(#coverSky)"/>
    <path d="M0,650 C250,650 500,620 700,560 C850,515 1000,480 1120,470 L1120,724 L0,724Z" fill="url(#navyBand)"/>
    <circle cx="712" cy="610" r="250" fill="var(--bright)"/>
    <circle cx="868" cy="290" r="215" fill="url(#tentPhoto)" role="img" aria-label="Photo of a tent on the beach at sunset"/>
    <circle cx="985" cy="525" r="96" fill="url(#sunsetPhoto)" stroke="#fff" stroke-width="0" role="img" aria-label="Photo of a glowing tent on the sand at sunset"/>
  </svg>

  <div class="packages">
    <div class="package" style="top:30px">
      <div class="shot" style="top:12px;background:linear-gradient(180deg,#3e8fd6,#d7c7a6)" role="img" aria-label="Photo of campers with gear on the beach"></div>
      <div class="price" style="top:14px">Price<br>$445</div>
      <div class="info" style="top:6px">
        <h3>BRONZE CAMPING PACKAGE</h3>
        <ul>
          <li>Bring your own camping gear and supplies .</li>
          <li>Day charter from Port of Airlie, one snorkelling location, Bush walk to Hill Inlet lookout and Whitehaven Beach south.</li>
          <li>Overnight camp at one island location</li>
          <li>Camping permit fees</li>
        </ul>
      </div>
    </div>
    <div class="package" style="top:228px">
      <div class="shot" style="top:12px;background:linear-gradient(180deg,#6fa9d8,#3f5a55)" role="img" aria-label="Photo of a swag tent under trees by the sea"></div>
      <div class="price" style="top:14px">Price<br>$535</div>
      <div class="info" style="top:0">
        <h3>SILVER CAMPING PACKAGE</h3>
        <ul>
          <li>Double or single swag</li>
          <li>All bed linen</li>
          <li>chair</li>
          <li>All Meals ( Day 1 Lunch, Day 2 Dinner, Day 3 Breakfast</li>
          <li>Day charter from Port of Airlie, one snorkelling location, Bush walk to Hill Inlet 9.00am to 3.00 pm lookout and Whitehaven Beach south</li>
          <li>Overnight camp at one island location 3.00pm t0 11.am</li>
          <li>Camping permit fees</li>
          <li>Use of non-motorised water sports</li>
        </ul>
      </div>
    </div>
    <div class="package" style="top:436px">
      <div class="shot" style="top:12px;background:linear-gradient(90deg,#c9481c,#9fd0ee 30%,#9fd0ee 70%,#c9481c)" role="img" aria-label="Photo of the beach seen from inside an open tent"></div>
      <div class="price" style="top:14px">Price<br>$650</div>
      <div class="info" style="top:0">
        <h3>GOLD CAMPING PACKAGE</h3>
        <ul>
          <li>Trailhaven pro 4 person tent</li>
          <li>Raised stretchers</li>
          <li>All bed linen</li>
          <li>Light</li>
          <li>Table, chairs, drinks esky with ice</li>
          <li>All Meals ( Day 1 Lunch, Day 2 Dinner, Day 3 Breakfast )</li>
          <li>Day charter from Port of Airlie, one snorkelling location, Bush walk to Hill Inlet 9.00am to 3.00 pm lookout and Whitehaven Beach south</li>
          <li>Overnight camp at one island location 3.00pm t0 11.am<br>Camping permit fees<br>Use of non-motorised water sports</li>
        </ul>
      </div>
    </div>
    <div class="extras">Extras – Fishing tackle and bait</div>
    <div class="extras-price">$50</div>
  </div>

  <div class="brand" style="left:805px;top:58px;font-size:26px"><span class="dot"></span>Coral Trek</div>

  <div class="headline">
    <div class="lead">Day charter and</div>
    <div class="big">Overnight</div>
    <div class="big">Camping</div>
    <div class="mid">Whit Ehaven</div>
    <div class="huge">Beach</div>
  </div>
</section>

<section class="spread spread--inside" aria-label="Inner spread: itinerary and camping locations">
  <svg class="bg" viewBox="0 0 1120 724" width="1120" height="724">
    <defs>
      <linearGradient id="groupPhoto" x1="0" y1="0" x2="1" y2="0"><stop offset="0" stop-color="#c98a4a"/><stop offset=".5" stop-color="#d9a76a"/><stop offset="1" stop-color="#8a6f57"/></linearGradient>
      <linearGradient id="beachSunset" x1="0" y1="0" x2="0" y2="1"><stop offset="0" stop-color="#5d6f8e"/><stop offset=".35" stop-color="#e58a3a"/><stop offset="1" stop-color="#4a2a22"/></linearGradient>
      <linearGradient id="seaPhoto" x1="0" y1="0" x2="1" y2="1"><stop offset="0" stop-color="#2a8fb0"/><stop offset=".5" stop-color="#bfe3ec"/><stop offset="1" stop-color="#1d7fa8"/></linearGradient>
      <linearGradient id="lagoonPhoto" x1="0" y1="0" x2="0" y2="1"><stop offset="0" stop-color="#2f86e0"/><stop offset=".6" stop-color="#22c2cf"/><stop offset="1" stop-color="#eaf6f4"/></linearGradient>
      <linearGradient id="tentView" x1="0" y1="0" x2="1" y2="0"><stop offset="0" stop-color="#1b5fae"/><stop offset=".25" stop-color="#8fc3e4"/><stop offset=".75" stop-color="#8fc3e4"/><stop offset="1" stop-color="#1b5fae"/></linearGradient>
    </defs>
    <rect x="0" y="0" width="560" height="724" fill="var(--deep)"/>
    <path d="M0,0 L560,0 L560,200 C460,270 300,300 180,290 C100,283 40,265 0,250Z" fill="url(#groupPhoto)" role="img" aria-label="Photo of friends around a campsite playing guitar"/>
    <path d="M0,250 C40,265 100,283 180,290 C300,300 460,270 560,200 L560,214 C460,284 300,312 180,302 C100,296 40,278 0,262Z" fill="var(--navy)"/>
    <rect x="0" y="510" width="560" height="214" fill="url(#beachSunset)" role="img" aria-label="Photo of people cheering on the beach at sunset"/>
    <rect x="560" y="0" width="560" height="724" fill="#fff"/>
    <path d="M560,0 L1120,0 L1120,200 C950,260 760,285 560,270Z" fill="url(#seaPhoto)" role="img" aria-label="Photo of a charter boat speeding across turquoise water"/>
    <path d="M560,724 L560,560 C700,480 950,470 1120,520 L1120,724Z" fill="var(--sky)"/>
    <path d="M570,724 L570,575 C710,500 950,492 1120,540 L1120,724Z" fill="url(#tentView)" role="img" aria-label="Photo of a woman sitting in a tent looking at the beach"/>
    <circle cx="109" cy="427" r="74" fill="none" stroke="#888" stroke-width="1.5" stroke-dasharray="4 3"/>
    <circle cx="109" cy="427" r="66" fill="#4a9fd6" role="img" aria-label="Photo of a snorkeller in a mask"/>
    <circle cx="970" cy="364" r="92" fill="none" stroke="#888" stroke-width="1.5" stroke-dasharray="4 3"/>
    <circle cx="970" cy="364" r="84" fill="url(#lagoonPhoto)" role="img" aria-label="Photo of white sand swirling through a turquoise inlet"/>
  </svg>

  <div class="itinerary">
    <h2>ITINERARY</h2>
    <div class="steps">
      <div class="time">9.00AM</div>
      <p>Start your adventure from the Port of Airlie marina , at</p>
      <p>Explore the Whitsundays for the day on our high-speed adventure vessel</p>
      <p>Day charter includes one snorkelling location, Hill Inlet lookout Bush walk and Whitehaven Beach</p>
      <div class="time">3.00pm</div>
      <p>Arrive at the overnight camping location</p>
      <div class="time">11.00AM</div>
      <p>Depart the overnight camping location</p>
    </div>
  </div>

  <div class="brand" style="left:572px;top:20px;width:228px;height:88px;background:#fff;padding-left:18px;font-size:28px"><span class="dot"></span>Coral Trek</div>

  <div class="locations">
    <h2>Camping<br>Locations</h2>
    <table>
      <tr><td>Dugong Beach</td><td>Max 18 People</td></tr>
      <tr><td>Sandy Bay camp</td><td>Max 18 People</td></tr>
      <tr class="gap"><td>Henning Island</td><td>Max 9 People</td></tr>
      <tr><td>Maureens Cove</td><td>Max 12 people</td></tr>
      <tr class="gap"><td>Whitehaven Beach</td><td>Max 12 people</td></tr>
    </table>
  </div>
</section>

</body>
</html>
```